Local Flower Farm Needs Business Card Design

I need business cards designed for a flower farm based in Eudora, Kansas.
Business Info:
We are a local cut flower farm located in Eudora, Kansas, founded by Corinne Haldwick. What started as a passion for agriculture and search for more joy in daily life has blossomed into a small business dedicated to providing the community with beautiful, fresh, and sustainable flowers. We specialize in local, seasonal blooms, ensuring that every petal reflects the care and dedication we pour into our craft. Our mission is to deliver the highest quality flowers directly to our customers through local farmers markets and to florists who share our commitment to sustainability. Join us in celebrating the beauty of nature, one bloom at a time!
Contact Details:
Corinne Haldwick
Owner
Phone 913-555-0147
Facebook: Rosalind Thorpe Gardens
Instagram: @RosalindThorpeGardens
Website: RosalindThorpeGardens.example
Target Market(s)
Wholesale to Florists and Direct to Consumer via Farmers Market
Industry/Entity Type
Florist, Farm
Contact Information for Business Card
Name, Contact Info, Logo
Look and feel
Each slider illustrates characteristics of the customer's brand and the style your logo design should communicate.

```html
<!DOCTYPE html>
<html lang="en">
<head>
<meta charset="utf-8">
<title>Rosalind Thorpe Gardens — Business Card</title>
<link href="https://fonts.googleapis.com/css2?family=Libre+Baskerville:wght@400;700&display=swap" rel="stylesheet">
<style>
  :root {
    --bg: #2b2b2d;
    --teal-deep: #0b242a;
    --teal-back: #0e2d33;
    --teal-faint: #1a4048;
    --paper: #ffffff;
    --ink-light: #f3f5f5;
  }
  * { margin: 0; padding: 0; box-sizing: border-box; }
  html, body {
    width: 1200px; height: 689px; overflow: hidden;
    background: var(--bg);
    font-family: "Libre Baskerville", Georgia, serif;
  }
  .stage { position: relative; width: 1200px; height: 689px; }
  .card {
    position: absolute; top: 190px;
    width: 540px; height: 309px;
    border-radius: 26px; overflow: hidden;
    box-shadow: 0 18px 40px rgba(0,0,0,0.45);
  }
  /* Back of card */
  .card--back { left: 40px; background: var(--teal-back); }
  .back-mark {
    position: absolute; left: 50%; top: 50%;
    width: 200px; height: 200px; margin: -100px 0 0 -100px;
    border: 1.5px solid var(--teal-faint); border-radius: 50%;
    display: flex; align-items: center; justify-content: center;
    text-align: center;
  }
  .back-mark__name {
    color: var(--teal-faint); font-size: 17px; line-height: 1.45;
    letter-spacing: 0.12em; text-transform: uppercase;
  }
  /* Front of card */
  .card--front { left: 620px; background: var(--teal-deep); }
  .front-art { position: absolute; inset: 0; }
  .brand-mark {
    position: absolute; left: 317px; top: 7px;
    width: 176px; height: 176px;
    border: 1px solid var(--teal-deep); border-radius: 50%;
    display: flex; align-items: center; justify-content: center; text-align: center;
  }
  .brand-mark__name {
    color: var(--teal-deep); font-size: 14px; line-height: 1.5;
    letter-spacing: 0.12em; text-transform: uppercase;
  }
  .person {
    position: absolute; left: 34px; top: 112px; color: var(--ink-light);
  }
  .person__name { font-weight: 700; font-size: 22px; letter-spacing: 0.01em; white-space: nowrap; }
  .person__role { font-size: 12px; margin-top: 4px; margin-left: 18px; }
  .contact {
    position: absolute; left: 34px; bottom: 26px;
    list-style: none; color: var(--ink-light); font-size: 12px;
  }
  .contact__item { display: flex; align-items: center; gap: 8px; margin-top: 6px; white-space: nowrap; }
  .contact__icon { width: 13px; height: 13px; flex: none; }
  .contact__dot {
    width: 11px; height: 11px; margin: 0 1px; flex: none;
    border-radius: 2px; background: var(--ink-light);
  }
</style>
</head>
<body>
<main class="stage">
  <section class="card card--back" aria-label="Card back">
    <div class="back-mark">
      <span class="back-mark__name">Rosalind<br>Thorpe<br>Gardens</span>
    </div>
  </section>

  <section class="card card--front" aria-label="Card front">
    <svg class="front-art" width="540" height="309" viewBox="0 0 540 309" aria-hidden="true">
      <rect x="405" y="0" width="135" height="150" fill="var(--paper)"/>
      <circle cx="405" cy="95" r="125" fill="var(--paper)"/>
      <circle cx="405" cy="95" r="133" fill="none" stroke="var(--paper)" stroke-width="3" stroke-dasharray="279 900" transform="rotate(70 405 95)"/>
    </svg>
    <div class="brand-mark">
      <span class="brand-mark__name">Rosalind<br>Thorpe<br>Gardens</span>
    </div>

    <div class="person">
      <p class="person__name">Corinne Haldwick</p>
      <p class="person__role">Owner</p>
    </div>

    <ul class="contact">
      <li class="contact__item">
        <svg class="contact__icon" viewBox="0 0 16 16" aria-hidden="true"><path d="M4 1.5 6.3 5 5 6.6c.9 1.8 2.4 3.3 4.4 4.4L11 9.7l3.5 2.3-1.2 2.5C7 14.2 1.8 9 1.5 2.7Z" fill="var(--ink-light)"/></svg>
        <span>913-555-0147</span>
      </li>
      <li class="contact__item">
        <svg class="contact__icon" viewBox="0 0 16 16" aria-hidden="true"><circle cx="8" cy="8" r="6.5" fill="none" stroke="var(--ink-light)" stroke-width="1.4"/><path d="M1.5 8h13M8 1.5c-3 3.5-3 9.5 0 13M8 1.5c3 3.5 3 9.5 0 13" fill="none" stroke="var(--ink-light)" stroke-width="1.1"/></svg>
        <span>RosalindThorpeGardens.example</span>
      </li>
      <li class="contact__item">
        <span class="contact__dot" aria-hidden="true"></span>
        <span>Rosalind Thorpe Gardens</span>
      </li>
      <li class="contact__item">
        <span class="contact__dot" aria-hidden="true"></span>
        <span>@RosalindThorpeGardens</span>
      </li>
    </ul>
  </section>
</main>
</body>
</html>
```